Print design needed to improve the layout and look of some existing documents

We need someone to take a couple of existing documents that we have and make them look much better using our existing logo and corporate colors etc. We require these to be delivered in a format that will allow our staff to edit the content as necessary via Microsoft word for conversion once finalized into a PDF. Ideally, we will also be able to use this as a newsletter template or for other documents that might be required in our business. www.corvelleadvisory.com.au
Updates

Target Market(s)

Business owners, executives, retirees

Industry/Entity Type

Financial Service

Font styles to use
Serif

Requirements
Must have
• Design that uses our existing branding and colors. It also needs to be ina form that we can edit the content / update easily. Ideally the format / layout could also be used for other documents such as short newsletters etc.
Nice to have
• Fresh, simple and crisp. Very professional looking.
Should not have
• strange fonts, weird layouts.

```html
<!DOCTYPE html>
<html lang="en">
<head>
<meta charset="utf-8">
<title>Corvelle Advisory – Financial Services Guide</title>
<link href="https://fonts.googleapis.com/css2?family=Open+Sans:wght@400;600;700&display=swap" rel="stylesheet">
<style>
:root{
  --bg:#e4e4e4;
  --paper:#ffffff;
  --sheet:#f5f5f5;
  --blue:#1592d3;
  --bar:#1a9bd7;
  --green:#7ab648;
  --text:#474747;
  --label:#3b3b3b;
  --logo:#5a6570;
}
*{box-sizing:border-box;margin:0;padding:0}
html,body{width:1200px;height:793px;overflow:hidden;background:var(--bg)}
body{font-family:"Open Sans",Arial,sans-serif;color:var(--text);position:relative}
.page{position:absolute;top:36px;width:519px;height:728px;background:var(--paper)}
.page--left{left:70px}
.page--right{left:620px}
.sheet{position:absolute;left:17px;top:20px;width:486px;height:688px;background:var(--sheet)}
.brand{position:absolute;left:20px;top:28px;display:flex;align-items:center;gap:7px}
.brand__mark{width:14px;height:14px;background:var(--blue)}
.brand__name{font-size:17px;font-weight:400;letter-spacing:1.5px;color:var(--logo)}
.heading{position:absolute;top:66px;display:flex;align-items:center;gap:6px;font-size:13px;font-weight:700;color:var(--blue)}
.heading svg{width:14px;height:14px}
p{font-size:8.8px;line-height:11.4px;margin-bottom:11.5px}
.adviser{position:absolute;left:18px;width:452px}
.adviser__photo{position:absolute;left:0;top:0;width:83px;height:111px;background:linear-gradient(160deg,#9fb3c2 0%,#6f8597 55%,#3d4a58 100%)}
.adviser__label{position:absolute;left:0;bottom:0;width:100%;height:27px;background:var(--label);color:#fff;font-size:11.5px;font-weight:700;display:flex;align-items:center;justify-content:center}
.adviser__bio{position:absolute;left:95px;top:0;width:356px}
.column{position:absolute;top:92px;width:212px}
.column--process{left:18px}
.column--fees{left:255px}
.subhead{font-size:9px;font-weight:600;color:var(--blue);margin:-2px 0 6px}
.tight{margin-bottom:0}
.footer{position:absolute;left:0;bottom:0;width:100%;height:22px;background:var(--bar);display:flex;align-items:center;color:#fff;font-size:6.6px;padding-left:18px}
.footer__sep{margin:0 4px}
.footer__num{position:absolute;right:0;top:0;width:46px;height:22px;background:var(--green);font-size:12px;font-weight:700;display:flex;align-items:center;justify-content:center}
</style>
</head>
<body>

<section class="page page--left">
  <div class="sheet">
    <div class="brand"><span class="brand__mark"></span><span class="brand__name">CORVELLE ADVISORY</span></div>
    <h2 class="heading" style="left:19px">
      <svg viewBox="0 0 14 14"><circle cx="7" cy="7" r="6" fill="none" stroke="var(--green)" stroke-width="1.3"/><path d="M6 4.3 8.7 7 6 9.7" fill="none" stroke="var(--green)" stroke-width="1.4"/></svg>
      Your Financial Advisers
    </h2>

    <article class="adviser" style="top:106px">
      <div class="adviser__photo" role="img" aria-label="Portrait of adviser Grant Ashby"><div class="adviser__label">Grant Ashby</div></div>
      <div class="adviser__bio">
        <p>Grant Ashby is the Managing Director of Corvelle Advisory Pty Ltd.</p>
        <p>He has been providing financial planning and investment advice to clients since 1993. Prior to forming Corvelle Advisory, he has been director and part owner of Meridian Investment &amp; Retirement Services Pty Ltd since 1998.</p>
        <p>He holds a Bachelor of Business in Accounting &amp; Finance, a graduate diploma in Financial Planning and is a SFPA Retirement Fund Specialist Adviser. He is a member of the Financial Planners Guild (FPG), a Fellow of the Institute of Finance Professionals and is a member of the Society of Financial Advisers (SFA).</p>
      </div>
    </article>

    <article class="adviser" style="top:263px">
      <div class="adviser__photo" role="img" aria-label="Portrait of adviser Neil Hartwell"><div class="adviser__label">Neil Hartwell</div></div>
      <div class="adviser__bio">
        <p>Neil Hartwell has been providing financial planning and investment advice to clients since 1999.</p>
        <p>He has five years specific financial planning and investment advice experience and an additional 10 years in banking and general insurance.</p>
        <p>He holds an Advanced Diploma in Financial Planning, a Diploma in Finance/Mortgage Broking and is currently working towards completing a Bachelor of Commerce at Westbrook University.</p>
        <p>Grant Ashby, Peter Kovalenko and Neil Hartwell will provide these services to you as Authorised Representatives of Corvelle Advisory Pty Ltd. They act on behalf of Corvelle Advisory Pty Ltd which is responsible for the services they provide.</p>
      </div>
    </article>

    <article class="adviser" style="top:454px">
      <div class="adviser__photo" role="img" aria-label="Portrait of adviser Peter Kovalenko"><div class="adviser__label">Peter Kovalenko</div></div>
      <div class="adviser__bio">
        <p>Peter Kovalenko chairs the investment committee of Corvelle Advisory Pty Ltd.</p>
        <p>He has many decades of experience in the financial services industry. He was Director Private Banking at Harbourview Bank from 2009 to 2010 and was State Manager Broker Mortgage Services at Harbourview Bank from 2005 to 2006. He also held a variety of senior positions within the Eastgate Bank of Australia where he served as an employee for over 30 years.</p>
        <p>He has extensive management and leadership skills and he holds a Diploma of Financial Planning from the Coastal Institute of Technology.</p>
      </div>
    </article>

    <footer class="footer">
      Corvelle Advisory Pty Ltd<span class="footer__sep">•</span>AFSL 480217<span class="footer__sep">•</span>ABN 52 713 094 268<span class="footer__sep"></span>&#128279;&nbsp;www.corvelleadvisory.com.au
      <span class="footer__num">2</span>
    </footer>
  </div>
</section>

<section class="page page--right">
  <div class="sheet">
    <div class="brand"><span class="brand__mark"></span><span class="brand__name">CORVELLE ADVISORY</span></div>
    <h2 class="heading" style="left:19px">
      <svg viewBox="0 0 14 14"><circle cx="7" cy="7" r="6" fill="none" stroke="var(--green)" stroke-width="1.3"/><path d="M6 4.3 8.7 7 6 9.7" fill="none" stroke="var(--green)" stroke-width="1.4"/></svg>
      The financial advice process
    </h2>
    <h2 class="heading" style="left:256px">
      <svg viewBox="0 0 14 14"><circle cx="7" cy="7" r="6" fill="none" stroke="var(--green)" stroke-width="1.3"/><path d="M6 4.3 8.7 7 6 9.7" fill="none" stroke="var(--green)" stroke-width="1.4"/></svg>
      Fees
    </h2>

    <div class="column column--process">
      <p>We recognise that the objectives and personal circumstances of each client are different.</p>
      <p>We understand that what is right for one client may not be right for another.</p>
      <p>We will listen to you to understand your objectives and circumstances. We will also ask questions to make sure we address all relevant issues.</p>
      <p>When we first provide advice to you it will be explained thoroughly and documented in a Statement of Advice which you can take away and study.</p>
      <p>The Statement of Advice will explain the basis for the advice, the cost to you of implementing the advice and any fees associated with the advice.</p>
      <p>For insurance and managed funds (except under the MDA service) recommendations, we will provide you with a Product Disclosure Statement. This contains information to help you understand the product being recommended.</p>
      <p>At all times you are able to contact us and ask questions about the advice and investments recommended.</p>
      <p>You can provide instructions to us in writing, via phone or via email/fax. Please note you are responsible for ensuring your instructions do actually reach us.</p>
      <p class="tight">We may provide further advice to you to keep your plan up to date with changes in your circumstances, changes in the law and changes in the economy and investments.</p>
      <p>The further advice we provide will be dependent on the Terms of Engagement you sign with us. It will be documented in a Record of Advice.</p>
    </div>

    <div class="column column--fees">
      <p style="margin-bottom:14px">All fees are payable to Corvelle Private Advisory Pty Ltd as Trustee for Fairhaven Trust.</p>
      <p style="line-height:13px;margin-bottom:13px">Grant Ashby is a beneficiary of Fairhaven Trust and shares in the profits of the business.</p>
      <p style="line-height:13px;margin-bottom:13px">Peter Kovalenko and Neil Hartwell are employees of Corvelle Private Advisory Pty Ltd as Trustee for Fairhaven Trust. They will be paid a salary and may receive a performance bonus which amongst other items will be based on the revenue they generate for the business.</p>
      <p style="line-height:13px;margin-bottom:15px">Your first meeting with us is complimentary and obligation free.</p>
      <h3 class="subhead">Plan Preparation Fee</h3>
      <p>The Plan Preparation fee includes all meetings with you, the time we take to determine our advice and the production of the SoA.</p>
      <p>The Plan Preparation fee is based on the scope and complexity of advice provided to you. We will agree the fee with you at our first meeting or shortly after.</p>
      <h3 class="subhead">Plan Implementation Fee</h3>
      <p style="margin-bottom:17px">If you decide to proceed with our advice we may charge a fee for the time we spend assisting you with implementation. We will let you know what the fee will be in the SoA.</p>
      <h3 class="subhead">Ongoing Services Fees</h3>
      <p>Once your investments are established we may provide you with ongoing services.</p>
      <p>Ongoing fees will depend on the services we provide to you. They may be a percentage of the transaction value, an agreed fixed fee or a percentage of your portfolio value.</p>
      <p>The services and fees will be set out in the SoA or RoA that we provide to you.</p>
    </div>

    <footer class="footer">
      Corvelle Advisory Pty Ltd<span class="footer__sep">•</span>AFSL 480217<span class="footer__sep">•</span>ABN 52 713 094 268<span class="footer__sep"></span>&#128279;&nbsp;www.corvelleadvisory.com.au
      <span class="footer__num">3</span>
    </footer>
  </div>
</section>

</body>
</html>
```